Hartwell Estates Business Cards

I would like a business card that includes myself and my partner.
Includes: Logo, office #, email, website, our names, our numbers and possibly the address. I would also like the logo to be embossed and the card to be horizontal.
There is a photo of our yard signs to give you an idea of the colors of our business.

Target Market(s)

Everyone in real estate market.
We are in a rural area. Our clientele are from all socioeconomic backgrounds.

Industry/Entity Type

Real Estate Agent

Contact Information for Business Card

Company Name: Hartwell Estates
Our Names, Titles & Cell #'s : Dana Pembrook-Broker (555).317.6624, Marla Pembrook-Realtor (555).609.1385
Office #: (555).240.3918
Website: hartwellestates-demo.com
Joint Email: pembrook@hartwellestates-demo.com
Office Address: 418B W. Calloway Ave.
Cedar Fork, NM. 70913

Font styles to use
Serif

Requirements
Must have
• HORIZONTAL, Logo, Myself and my partners names, Our cell #'s, our office #, our website, our email address
Nice to have
• Embossed logo, office address, our titles.

```html
<!DOCTYPE html>
<html lang="en">
<head>
<meta charset="utf-8">
<title>Hartwell Estates Business Card</title>
<link rel="stylesheet" href="https://fonts.googleapis.com/css2?family=Montserrat:wght@400;500;600&display=swap">
<style>
  :root {
    --bg: #ecebe8;
    --card: #fbfbfa;
    --purple: #5a1a86;
    --purple-deep: #47106e;
    --grey: #6f6a60;
    --ink: #4a4540;
    --emboss: #d6d5d2;
  }
  html, body {
    margin: 0;
    width: 1200px;
    height: 1022px;
    overflow: hidden;
    background: var(--bg);
  }
  .card {
    position: absolute;
    left: 100px;
    top: 226px;
    width: 1000px;
    height: 570px;
    background: var(--card);
    border-radius: 22px;
    overflow: hidden;
    box-shadow: 0 2px 10px rgba(0,0,0,0.12);
    font-family: "Montserrat", Arial, sans-serif;
  }
  .card__band {
    position: absolute;
    inset: 0;
  }
  .brand {
    position: absolute;
    left: 70px;
    top: 110px;
    display: flex;
    align-items: center;
    gap: 32px;
  }
  .brand__dot {
    width: 96px;
    height: 96px;
    border-radius: 50%;
    background: var(--purple);
  }
  .brand__name {
    color: var(--emboss);
    font-weight: 500;
    line-height: 1.05;
    text-transform: uppercase;
  }
  .brand__name .line1 { display: block; font-size: 52px; letter-spacing: 4px; }
  .brand__name .line2 { display: block; font-size: 26px; letter-spacing: 10px; margin-top: 6px; }
  .rule {
    position: absolute;
    left: 210px;
    top: 276px;
    width: 390px;
    height: 2px;
    background: var(--purple);
  }
  .agents {
    position: absolute;
    right: 40px;
    top: 226px;
    text-align: right;
  }
  .agent { margin-bottom: 14px; }
  .agent__name {
    color: var(--purple);
    font-weight: 600;
    font-size: 34px;
    line-height: 1.15;
  }
  .agent__title {
    color: var(--grey);
    font-size: 19px;
    line-height: 1.3;
  }
  .agent__phone {
    color: var(--purple);
    font-size: 21px;
    line-height: 1.3;
  }
  .office {
    position: absolute;
    left: 196px;
    top: 300px;
    color: var(--purple);
    font-size: 20px;
  }
  .office__address {
    margin: 0 0 14px 28px;
    line-height: 1.35;
  }
  .office__row {
    display: flex;
    align-items: center;
    gap: 12px;
    height: 31px;
  }
  .office__row svg { width: 16px; height: 16px; }
  .office__web { color: var(--ink); font-weight: 600; }
</style>
</head>
<body>
  <div class="card">
    <svg class="card__band" width="1000" height="570" viewBox="0 0 1000 570" aria-hidden="true">
      <polygon points="560,570 602,498 1000,498 1000,570" fill="var(--purple-deep)"/>
    </svg>

    <div class="brand">
      <div class="brand__dot"></div>
      <div class="brand__name">
        <span class="line1">Hartwell</span>
        <span class="line2">Estates</span>
      </div>
    </div>

    <div class="rule"></div>

    <div class="agents">
      <div class="agent">
        <div class="agent__name">Dana Pembrook</div>
        <div class="agent__title">Broker</div>
        <div class="agent__phone">(555).317.6624</div>
      </div>
      <div class="agent">
        <div class="agent__name">Marla Pembrook</div>
        <div class="agent__title">Realtor</div>
        <div class="agent__phone">(555).609.1385</div>
      </div>
    </div>

    <div class="office">
      <div class="office__address">418B W. Calloway Ave.<br>Cedar Fork, NM. 70913</div>
      <div class="office__row">
        <svg viewBox="0 0 16 16" aria-hidden="true"><path d="M4 1.5 L6.5 4.5 L5 6.2 C6 8.4 7.6 10 9.8 11 L11.5 9.5 L14.5 12 L12.8 14.3 C7 13.5 2.5 9 1.7 3.2 Z" fill="none" stroke="var(--grey)" stroke-width="1.3" stroke-linejoin="round"/></svg>
        <span>(555).240.3918</span>
      </div>
      <div class="office__row">
        <svg viewBox="0 0 16 16" aria-hidden="true"><rect x="1.5" y="3.5" width="13" height="9" fill="none" stroke="var(--grey)" stroke-width="1.3"/><path d="M1.5 3.5 L8 9 L14.5 3.5" fill="none" stroke="var(--grey)" stroke-width="1.3"/></svg>
        <span>pembrook@hartwellestates-demo.com</span>
      </div>
      <div class="office__row">
        <svg viewBox="0 0 16 16" aria-hidden="true"><circle cx="8" cy="8" r="6.3" fill="none" stroke="var(--grey)" stroke-width="1.3"/><ellipse cx="8" cy="8" rx="2.8" ry="6.3" fill="none" stroke="var(--grey)" stroke-width="1.1"/><path d="M1.7 8 H14.3" stroke="var(--grey)" stroke-width="1.1"/></svg>
        <span class="office__web">www.hartwellestates-demo.com</span>
      </div>
    </div>
  </div>
</body>
</html>
```